Branding product image: VELMOT (Golden Papaya) in Plastic Cup (Ready to Eat)

The product is sliced Fruit in Light syrup
Flavour: VELMOT (Golden Papaya)
The temporary product name: VELMOT
I want the product design to be something 'fun', 'natural', and 'colourful'
The design concept could be anything depends on your imagination, but it must be eye catchy and attractive.
Basically, I want you to be creative in designing the logo and the overall graphic design for the label.
The measurement is 20 cm (Length) x 6,5 cm (Height)
The target customers are young and health conscious audiences (10 years - 65 years old).
Create something different. Something extraordinary.
Brief summary about the fruit:
This fruit only grows in certain part of the world. It grows in mountain area that is in tropical climate. The fruit flesh has a yellowish-golden color. It has an extraordinary taste (unlike normal papaya) and it suits very well with any dishes from cold appetizer, white/ red meat, desserts, and cocktails.
I need a packaging design for Fruit Cup productThe product is sliced Fruit in Light syrup.There will be various flavours i.e. apple, lychee, peach, papaya, etc.However, you may design the product using one sample flavour (i.e. papaya) first, as the designs of other flavours could be adjusted afterwards.The temporary product name is: RICCANAI want the product design to be something 'fun', 'natural', and 'colourful'.The design concept could be anything depends on your imagination. Basically, I want you to be creative in designing the logo and the overall graphic design for the label. - Create something different. Something extraordinary -Additional:The measurement is 20cm (Length) x 5cm (Height).The target customers are young audiences (10 years - 35 years old).The product design must stand out in the supermarket shelf.It must be eye catchy and attractive.Thank you,Jordan-PLEASE REFER TO DESIGN SAMPLE ATTACHED TO HAVE A BETTER UNDERSTANDING FOR THE PRODUCT CONCEPT- Added Wednesday, September 17, 2014
Project Deadline Extended Reason: Haven't found a good design. Added Friday, September 19, 2014
Project Deadline Extended Reason: Need more time for designers to finalize and perfect the design.Thank you,Jordan Added Monday, September 29, 2014
Project Deadline Extended Reason: I haven't found a great design yet. Added Tuesday, February 24, 2015
Reason: Getting better designs now. Still Open to new ideas while refining the latest designs from some designers.
Please do your best in submitting other great designs!

```html
<!DOCTYPE html>
<html lang="en">
<head>
<meta charset="utf-8">
<title>DOSUVEL Golden Papaya in Light Syrup – Cup Label</title>
<link rel="stylesheet" href="https://fonts.googleapis.com/css2?family=Asap:wght@600&family=Lato:wght@400&family=Sriracha&display=swap">
<style>
  :root {
    --page-bg: #eef1f3;
    --band-blue: #2eaee0;
    --band-blue-deep: #1e96c8;
    --sky-light: #f3f7f2;
    --sky-mint: #dcebd6;
    --leaf-green: #8cc653;
    --leaf-soft: #c4e29b;
    --brand-indigo: #3b3fa6;
    --gold-line: #d8b35f;
    --gold-light: #f4e2ae;
    --papaya-orange: #f0961c;
    --papaya-yellow: #f8c54c;
    --mark-dark: #1b1b1d;
    --white: #ffffff;
  }
  * { margin: 0; padding: 0; box-sizing: border-box; }
  html, body {
    width: 1200px; height: 679px; overflow: hidden;
    background: var(--page-bg);
  }
  .label {
    position: absolute; left: 82px; top: 47px;
    width: 1035px; height: 585px;
    overflow: hidden;
    background:
      radial-gradient(ellipse 40% 45% at 50% 40%, var(--white) 0%, rgba(255,255,255,0) 100%),
      linear-gradient(180deg, var(--sky-light) 0%, var(--sky-mint) 100%);
  }
  .label__top-band {
    position: absolute; left: 0; top: 0; width: 100%; height: 22px;
    background: var(--band-blue);
  }
  .foliage { position: absolute; }
  .foliage--left {
    left: 0; top: 22px; width: 150px; height: 260px;
    background: radial-gradient(ellipse 80% 70% at 30% 35%, var(--leaf-green) 0%, var(--leaf-soft) 45%, rgba(196,226,155,0) 100%);
  }
  .foliage--right {
    right: 0; top: 22px; width: 140px; height: 280px;
    background: radial-gradient(ellipse 80% 70% at 70% 45%, var(--leaf-green) 0%, var(--leaf-soft) 45%, rgba(196,226,155,0) 100%);
  }
  .foliage--top-left {
    left: 150px; top: 22px; width: 320px; height: 70px;
    background: radial-gradient(ellipse 60% 70% at 50% 20%, var(--leaf-soft) 0%, rgba(196,226,155,0) 100%);
  }
  .foliage--top-right {
    left: 680px; top: 22px; width: 220px; height: 80px;
    background: radial-gradient(ellipse 60% 70% at 50% 25%, var(--leaf-soft) 0%, rgba(196,226,155,0) 100%);
  }
  .maker-mark {
    position: absolute; left: 48px; top: 222px;
    display: flex; align-items: center; gap: 10px;
  }
  .maker-mark__dot {
    width: 34px; height: 34px; border-radius: 50%;
    background: var(--mark-dark);
  }
  .maker-mark__name {
    font-family: "Lato", sans-serif; font-size: 26px;
    color: var(--mark-dark);
  }
  .brand-name {
    position: absolute; left: 214px; top: 72px;
    font-family: "Asap", sans-serif; font-weight: 600;
    font-size: 178px; line-height: 1; letter-spacing: 1px;
    color: var(--brand-indigo);
    text-shadow: 0 3px 5px rgba(40,40,90,.18);
  }
  .flavour {
    position: absolute; left: 226px; top: 296px;
    font-family: "Sriracha", cursive; font-size: 42px; line-height: 55px;
    color: var(--brand-indigo);
  }
  .label__gold-line {
    position: absolute; left: 0; top: 452px; width: 100%; height: 9px;
    background: linear-gradient(90deg, var(--gold-line), var(--gold-light) 50%, var(--gold-line));
  }
  .label__bottom-band {
    position: absolute; left: 0; top: 461px; width: 100%; height: 124px;
    background: linear-gradient(180deg, var(--band-blue), var(--band-blue-deep));
  }
  .net-weight {
    position: absolute; left: 243px; top: 496px;
    font-family: "Lato", sans-serif; font-size: 24px;
    color: var(--white);
  }
  .fruit-photo {
    position: absolute; left: 565px; top: 298px;
    width: 340px; height: 236px; border-radius: 50%;
    background: radial-gradient(ellipse at 50% 45%, var(--papaya-yellow) 0%, var(--papaya-orange) 65%, rgba(240,150,28,0) 100%);
  }
</style>
</head>
<body>
  <main class="label">
    <div class="label__top-band"></div>
    <div class="foliage foliage--left" role="img" aria-label="Fresh green leaves in soft sunlight"></div>
    <div class="foliage foliage--right" role="img" aria-label="Fresh green leaves in soft sunlight"></div>
    <div class="foliage foliage--top-left" role="img" aria-label="Green leaves hanging along the top edge"></div>
    <div class="foliage foliage--top-right" role="img" aria-label="Green leaves hanging along the top edge"></div>

    <div class="maker-mark">
      <span class="maker-mark__dot"></span>
      <span class="maker-mark__name">Clearleaf</span>
    </div>

    <h1 class="brand-name">DOSUVEL</h1>
    <p class="flavour">Golden Papaya<br>in Light Syrup</p>

    <div class="label__gold-line"></div>
    <div class="label__bottom-band"></div>
    <p class="net-weight">Net WT 6oz(170g)</p>

    <div class="fruit-photo" role="img" aria-label="Photo of two halves of a golden papaya with dark seeds"></div>
  </main>
</body>
</html>
```